Business Card Design Project

Looking to update our business cards. We have a logo with our slogan. We are an IT firm so we wouldlike a modern look.

Industry/Entity Type

Business

```html
<!DOCTYPE html>
<html lang="en">
<head>
<meta charset="utf-8">
<title>Lumora Inc – Business Card</title>
<link rel="stylesheet" href="https://fonts.googleapis.com/css2?family=Jost:wght@400;500;600;700&display=swap">
<style>
  :root {
    --green: #6b8440;
    --green-deep: #5f7b36;
    --green-text: #5f7b36;
    --lime: #a9c23f;
    --ink: #2a2a2a;
    --white: #ffffff;
    --backdrop: #ecebe6;
  }
  * { margin: 0; padding: 0; box-sizing: border-box; }
  html, body {
    width: 1200px; height: 699px; overflow: hidden;
    background: var(--backdrop);
    font-family: "Jost", "Helvetica Neue", Arial, sans-serif;
  }
  .canvas { position: relative; width: 1200px; height: 699px; }
  .card {
    position: absolute; width: 540px; height: 310px; top: 195px;
    overflow: hidden; box-shadow: 0 6px 18px rgba(0,0,0,0.18);
  }
  .card--front { left: 45px; background: var(--white); }
  .card--back { left: 615px; background: var(--green); }

  .card__band {
    position: absolute; inset: 0;
    background: linear-gradient(160deg, var(--green) 0%, var(--green-deep) 100%);
    clip-path: polygon(540px 82px, 540px 310px, 0 310px, 0 275px, 260px 230px, 360px 120px);
  }

  .brand { position: absolute; }
  .brand__name {
    font-weight: 600; letter-spacing: 6px; line-height: 1;
    display: flex; align-items: center; gap: 10px;
  }
  .brand__dot { width: 14px; height: 14px; border-radius: 50%; }
  .brand__tagline {
    font-weight: 600; letter-spacing: 3.4px; line-height: 1; margin-top: 8px;
  }
  .card--front .brand { left: 34px; top: 52px; color: var(--green-text); }
  .card--front .brand__name { font-size: 52px; }
  .card--front .brand__dot { background: var(--green-text); }
  .card--front .brand__tagline { font-size: 14.5px; color: var(--ink); }

  .holder { position: absolute; left: 40px; top: 182px; }
  .holder__name { font-size: 20px; font-weight: 600; color: var(--green-text); }
  .holder__title { font-size: 14px; color: var(--lime); margin-top: -2px; }

  .contacts {
    position: absolute; right: 30px; top: 112px; list-style: none;
    color: var(--white); font-size: 13.5px; text-align: right;
  }
  .contacts li { display: flex; align-items: center; justify-content: flex-end; gap: 6px; height: 21px; }
  .contacts svg { width: 12px; height: 12px; fill: var(--white); }
  .address {
    position: absolute; right: 30px; top: 226px;
    color: var(--white); font-size: 13.5px;
  }

  .card--back .brand { left: 0; right: 0; top: 92px; text-align: center; color: var(--white); }
  .card--back .brand__name { font-size: 62px; justify-content: center; }
  .card--back .brand__dot { background: var(--white); }
  .card--back .brand__tagline { font-size: 16px; letter-spacing: 4.5px; margin-top: 12px; }
  .website {
    position: absolute; left: 0; right: 0; top: 232px; text-align: center;
    color: var(--white); font-size: 24px; font-weight: 500; letter-spacing: 4px;
  }
</style>
</head>
<body>
<div class="canvas">

  <section class="card card--front">
    <div class="card__band" role="img" aria-label="Decorative green wave band across the lower right of the card"></div>

    <div class="brand">
      <div class="brand__name">LUMORA<span class="brand__dot"></span></div>
      <div class="brand__tagline">MAKING TECHNOLOGY EASY</div>
    </div>

    <div class="holder">
      <div class="holder__name">Your Name</div>
      <div class="holder__title">Title</div>
    </div>

    <ul class="contacts">
      <li><svg viewBox="0 0 24 24"><path d="M6.6 10.8a15 15 0 0 0 6.6 6.6l2.2-2.2c.3-.3.7-.4 1-.2 1.1.4 2.3.6 3.6.6.6 0 1 .4 1 1V20c0 .6-.4 1-1 1A17 17 0 0 1 3 4c0-.6.4-1 1-1h3.5c.6 0 1 .4 1 1 0 1.3.2 2.5.6 3.6.1.3 0 .7-.2 1z"/></svg>0123 456789</li>
      <li><svg viewBox="0 0 24 24"><path d="M7 1h10a2 2 0 0 1 2 2v18a2 2 0 0 1-2 2H7a2 2 0 0 1-2-2V3a2 2 0 0 1 2-2zm0 3v14h10V4zm5 15.5a1.2 1.2 0 1 0 0 2.4 1.2 1.2 0 0 0 0-2.4z"/></svg>0123 456789</li>
      <li><svg viewBox="0 0 24 24"><path d="M2 5h20v14H2zm2 2v.5l8 5 8-5V7zm0 2.8V17h16V9.8l-8 5z"/></svg>info@lumora.com</li>
    </ul>
    <div class="address">00, Complex name, City, State 0042</div>
  </section>

  <section class="card card--back">
    <div class="brand">
      <div class="brand__name">LUMORA<span class="brand__dot"></span></div>
      <div class="brand__tagline">MAKING TECHNOLOGY EASY</div>
    </div>
    <div class="website">www.lumora.com</div>
  </section>

</div>
</body>
</html>
```